Fight Deflation with Seasonal General Merchandise - Tall Pine Traders & Advisors, Inc.

We are looking to create a Business to Business Advertising Concept that will appear in various trade publications within the US Supermarket Industry. The final concept will be adapted to be used in print, digital and direct mail mediums. For purposes of your submissions, please design as if it is for a 8.5" x 11" (vertical) print ad.

Using the creative elements and images attached for direction and inspiration, please submit your best concepts. The high resolution images shown have already been purchased from a stock photo house with the rights to use them for this campaign. While we like these images as well as the headlines provided, feel free to add your own suggestions or creativity if you wish.

Primarily, however, we'd like you to take the existing headlines and images and build off of them, incorporating solid use of font/text treatment and improving upon overall layout of the ad so that the end result is professional and engaging to the audience.

A note about the concept: Tall Pine Traders supplies US Grocery Store Chains with Seasonal General Merchandise. Currently and for the foreseeable future, grocers are battling the effects of deflationary pricing on key commodities such as Eggs/Dairy; Meat; Produce, etc... The result of this is that grocery prices are significantly lower than last year. While this is good for the consumers, it is not ideal for the retailers as they are making fewer sales and profits while selling the same or more product. The products Tall Pine Trader's sells to these grocers can help the retailer offset these lower prices by adding "incremental" sales and profits to the retailer. Our products range from items like Christmas decor and gift wrap, to outdoor items like patio furniture and grills. We are focusing on the Christmas theme because the ads will drop starting late November.

Target Market(s)

Senior Buyers and Top Executives at US Based Grocery Store Chains.

Industry/Entity Type

Business

Requirements
Must have
• See Project Description
• Open to all colors and fonts.
Nice to have
• See Project Description
Should not have
• See Project Description

```html
<!DOCTYPE html>
<html lang="en">
<head>
<meta charset="utf-8">
<title>Tall Pine Traders &amp; Advisors, Inc. — Seasonal General Merchandise Ad</title>
<link rel="stylesheet" href="https://fonts.googleapis.com/css2?family=Jost:wght@400;500;700&display=swap">
<style>
  :root {
    --page-bg: #e9e9e9;
    --red-light: #f01414;
    --red-dark: #b50000;
    --blue-light: #22b0f0;
    --blue-dark: #0a78cc;
    --photo-cream: #efe6d2;
    --photo-warm: #a88f66;
    --photo-white: #fbfaf6;
    --white: #ffffff;
  }
  * { box-sizing: border-box; margin: 0; padding: 0; }
  html, body { width: 1000px; height: 1200px; overflow: hidden; background: var(--page-bg); }
  body { font-family: "Jost", "Futura", sans-serif; color: var(--white); }

  .ad {
    position: absolute; left: 44px; top: 10px;
    width: 912px; height: 1180px; overflow: hidden;
    box-shadow: 0 4px 18px rgba(0,0,0,.25);
  }
  .ad-shapes { position: absolute; inset: 0; }

  .headline {
    position: absolute; right: 55px; top: 44px;
    font-weight: 700; font-size: 56px; line-height: 1.08;
    text-align: right; letter-spacing: 1px; text-transform: uppercase;
  }
  .subhead {
    position: absolute; right: 55px; top: 198px;
    font-weight: 400; font-size: 21px; line-height: 1.3; text-align: right;
  }

  .brand {
    position: absolute; left: 68px; top: 925px;
    display: flex; align-items: center; gap: 14px;
  }
  .brand-square { width: 56px; height: 56px; background: var(--white); }
  .brand-name { font-weight: 700; font-size: 30px; line-height: 1.05; }

  .showroom {
    position: absolute; left: 68px; top: 1032px;
    font-weight: 400; font-size: 19px; line-height: 1.3;
  }
  .phone {
    position: absolute; left: 650px; top: 1005px; width: 220px;
    display: flex; flex-direction: column; align-items: center; gap: 14px;
  }
  .phone-number { font-weight: 700; font-size: 29px; letter-spacing: .5px; }

  .contact {
    position: absolute; left: 68px; right: 40px; top: 1122px;
    display: flex; align-items: center; font-size: 19px;
  }
  .contact-name { font-weight: 700; margin-right: 18px; }
  .contact-title { flex: 1; }
  .contact-email { display: flex; align-items: center; gap: 8px; }
</style>
</head>
<body>
  <main class="ad">
    <svg class="ad-shapes" width="912" height="1180" viewBox="0 0 912 1180">
      <defs>
        <linearGradient id="red-band" x1="0" y1="0" x2="1" y2="1">
          <stop offset="0" stop-color="var(--red-light)"/>
          <stop offset="1" stop-color="var(--red-dark)"/>
        </linearGradient>
        <linearGradient id="blue-band" x1="0" y1="0" x2="1" y2="1">
          <stop offset="0" stop-color="var(--blue-light)"/>
          <stop offset="1" stop-color="var(--blue-dark)"/>
        </linearGradient>
        <radialGradient id="photo-tone" cx="0.5" cy="0.5" r="0.7">
          <stop offset="0" stop-color="var(--photo-white)"/>
          <stop offset="0.55" stop-color="var(--photo-cream)"/>
          <stop offset="1" stop-color="var(--photo-warm)"/>
        </radialGradient>
      </defs>
      <rect class="photo" width="912" height="1180" fill="url(#photo-tone)" role="img"
            aria-label="Photo: carton of white eggs, one wearing a small Santa hat, with white snowflake decorations"/>
      <polygon class="light-strip" points="0,300 269,246 912,392 912,376 269,235 0,289" fill="var(--white)" opacity=".7"/>
      <polygon class="red-band" points="0,0 912,0 912,376 269,235 0,289" fill="url(#red-band)"/>
      <polygon class="white-strip" points="0,800 599,920 912,858 912,871 599,934 0,812" fill="var(--white)"/>
      <polygon class="blue-band" points="0,812 599,934 912,871 912,1180 0,1180" fill="url(#blue-band)"/>
    </svg>

    <h1 class="headline">Scrambling to deal<br>with deflation?</h1>
    <p class="subhead">Hatch Eggstraordinary Profits<br>with Seasonal General Merchandise!</p>

    <div class="brand">
      <span class="brand-square"></span>
      <span class="brand-name">Tall Pine Traders<br>and Advisors, Inc.</span>
    </div>

    <p class="showroom">
      Visit our exciting Fall/Winter 2017 Showroom<br>
      representing over 4,000 items from 350 factories<br>
      Scheduling appointments now for January - March, 2017
    </p>

    <div class="phone">
      <svg width="52" height="52" viewBox="0 0 52 52" aria-hidden="true">
        <circle cx="26" cy="26" r="23" fill="none" stroke="var(--white)" stroke-width="3"/>
        <path d="M19 14c2 0 3 4 3 6s-2 2-2 3 4 7 6 8 1-2 3-2 6 1 6 3-1 5-4 5C22 37 15 28 15 20c0-3 2-6 4-6z" fill="var(--white)"/>
      </svg>
      <span class="phone-number">555-214-7730</span>
    </div>

    <p class="contact">
      <span class="contact-name">Contact Dana Whitfield,</span>
      <span class="contact-title">VP Business Development at</span>
      <span class="contact-email">
        <svg width="16" height="12" viewBox="0 0 16 12" aria-hidden="true">
          <rect x="1" y="1" width="14" height="10" fill="none" stroke="var(--white)" stroke-width="1.5"/>
          <path d="M1 1l7 6 7-6" fill="none" stroke="var(--white)" stroke-width="1.5"/>
        </svg>
        dwhitfield@tallpinetraders.com
      </span>
    </p>
  </main>
</body>
</html>
```